Roofing Contractor business card redesign

I want to redesign my business card with a fresh, eye catching concept

Target Market(s)

Residential Roofing Clients, potential employees, and subcontractors.

Industry/Entity Type

Business

Colors

Designer to choose colors to be used in the design.

Requirements
Nice to have
• I just want something that's more pleasing to the eye. You can use a combination of either / or of my logos.

```html
<!DOCTYPE html>
<html lang="en">
<head>
<meta charset="utf-8">
<title>Fair Hands Builders – Business Card</title>
<link href="https://fonts.googleapis.com/css2?family=Work+Sans:wght@400;700&display=swap" rel="stylesheet">
<style>
  :root {
    --backdrop: #2b2b2b;
    --brown: #45130f;
    --orange: #f7861f;
    --ink: #333333;
    --paper: #ffffff;
  }
  * { box-sizing: border-box; margin: 0; padding: 0; }
  html, body {
    width: 1200px; height: 930px; overflow: hidden;
    background: var(--backdrop);
    font-family: "Work Sans", sans-serif;
  }
  .card {
    position: absolute; left: 278px; width: 644px; height: 368px;
    border-radius: 22px; overflow: hidden;
    box-shadow: 0 6px 18px rgba(0,0,0,.45);
  }
  .card--front { top: 76px; background: var(--paper); }
  .card--back { top: 486px; background: var(--brown); }

  .front-brand {
    position: absolute; top: 48px; left: 0; width: 100%;
    display: flex; flex-direction: column; align-items: center; gap: 10px;
  }
  .brand-dot { width: 70px; height: 70px; border-radius: 50%; background: var(--brown); }
  .front-brand .brand-name {
    font-weight: 700; font-size: 22px; line-height: 1.15; color: var(--brown);
    text-align: center;
  }

  .divider {
    position: absolute; top: 228px; left: 36px; width: 572px; height: 1px;
    background: var(--orange);
  }
  .contacts {
    position: absolute; top: 247px; left: 36px; list-style: none;
    font-size: 17px; color: var(--ink); line-height: 20px;
  }
  .contacts li { display: flex; align-items: center; gap: 12px; }
  .contacts svg { width: 13px; height: 13px; fill: none; stroke: var(--orange); stroke-width: 2; }
  .person {
    position: absolute; top: 242px; right: 38px; text-align: right;
    color: var(--ink); font-size: 17.5px; line-height: 20px;
  }
  .person .name { color: var(--orange); font-size: 29px; line-height: 34px; }
  .address-band {
    position: absolute; top: 334px; left: 0; width: 100%; height: 26px;
    background: var(--brown); color: var(--paper);
    font-size: 16px; line-height: 26px; text-align: center;
  }
  .accent-band {
    position: absolute; top: 360px; left: 0; width: 100%; height: 8px;
    background: var(--orange);
  }

  .back-brand {
    position: absolute; top: 0; left: 0; width: 100%; height: 100%;
    display: flex; flex-direction: column; align-items: center; justify-content: center;
    color: var(--paper); font-weight: 700;
  }
  .back-brand .lockup { display: flex; align-items: center; gap: 16px; font-size: 60px; line-height: 1; }
  .back-brand .brand-dot { width: 92px; height: 92px; background: var(--paper); }
  .back-brand .tagline { font-size: 32px; margin-top: 14px; }
</style>
</head>
<body>
  <section class="card card--front">
    <div class="front-brand">
      <span class="brand-dot"></span>
      <span class="brand-name">Fair Hands<br>Builders, Inc.</span>
    </div>
    <div class="divider"></div>
    <ul class="contacts">
      <li><svg viewBox="0 0 14 14"><path d="M3 1 L5 4 L4 6 Q6 9 8 10 L10 9 L13 11 L11 13 Q5 12 1 3 Z"/></svg>(555) 210-4800</li>
      <li><svg viewBox="0 0 14 14"><rect x="3.5" y="1" width="7" height="12" rx="1.2"/><line x1="6" y1="11" x2="8" y2="11"/></svg>(555) 367-9120</li>
      <li><svg viewBox="0 0 14 14"><rect x="1" y="3" width="12" height="8"/><path d="M1 3 L7 8 L13 3"/></svg>dale@fairhandsbuild.com</li>
    </ul>
    <div class="person">
      <div class="name">Dale Rourke</div>
      <div>Keystone Certified Roof Inspector</div>
      <div>Licensed Property Adjuster</div>
    </div>
    <div class="address-band">4410 Cedar Bend Road Suite 118 Fairview, TX 75099</div>
    <div class="accent-band"></div>
  </section>

  <section class="card card--back">
    <div class="back-brand">
      <div class="lockup"><span>Fair Hands</span><span class="brand-dot"></span></div>
      <div class="tagline">Builders, Inc.</div>
    </div>
  </section>
</body>
</html>
```